Mother's Day Sale Banner Ad For Jewelry Site

We are looking for a designer to design a banner on our website advertising our Mother's Day Sale. I have enclosed a few pieces of jewelry we would like used in the ad. The ad size needs to be 1187 × 400. The ad should say:

Mother's Day Sale - Save 15% with Promo Code: LOVEMOM

Jewelry

```html
<!DOCTYPE html>
<html lang="en">
<head>
<meta charset="utf-8">
<title>Mother's Day Sale – Save 15% with Promo Code LOVEMOM</title>
<link rel="stylesheet" href="https://fonts.googleapis.com/css2?family=Montserrat:wght@500&family=Raleway:wght@400;500&display=swap">
<style>
  :root {
    --bg-light: #f8f5f1;
    --bg-warm: #efe5dc;
    --brown: #8b7058;
    --red: #c9323b;
    --band: rgba(255, 255, 255, 0.75);
    --tile-border: #d9545b;
    --tile-white: #ffffff;
    --gold-light: #e6cf9a;
    --gold-dark: #c9a35a;
  }
  * { box-sizing: border-box; margin: 0; padding: 0; }
  html, body { width: 1200px; height: 404px; overflow: hidden; }
  .banner {
    position: relative;
    width: 1200px;
    height: 404px;
    background: radial-gradient(ellipse at 40% 50%, var(--bg-light) 0%, var(--bg-light) 40%, var(--bg-warm) 100%);
    font-family: "Raleway", sans-serif;
  }
  .sale-label {
    position: absolute;
    left: 137px;
    top: 86px;
    width: 385px;
    height: 36px;
    background: linear-gradient(90deg, var(--band) 0%, rgba(255,255,255,0.9) 60%, rgba(255,255,255,0.3) 100%);
    font-family: "Montserrat", sans-serif;
    font-weight: 500;
    font-size: 22px;
    letter-spacing: 2.6px;
    color: var(--brown);
    line-height: 36px;
    padding-left: 20px;
  }
  .save-line {
    position: absolute;
    left: 232px;
    top: 130px;
    color: var(--brown);
    font-size: 52px;
    font-weight: 400;
    line-height: 1.1;
    white-space: nowrap;
  }
  .save-line .discount {
    color: var(--red);
    font-family: "Montserrat", sans-serif;
    font-weight: 500;
    font-size: 42px;
  }
  .promo-line {
    position: absolute;
    left: 166px;
    top: 200px;
    color: var(--brown);
    font-size: 37px;
    font-weight: 400;
    white-space: nowrap;
  }
  .promo-code {
    position: absolute;
    left: 150px;
    top: 250px;
    color: var(--red);
    font-family: "Montserrat", sans-serif;
    font-weight: 500;
    font-size: 64px;
    letter-spacing: 4px;
    white-space: nowrap;
  }
  .tile {
    position: absolute;
    width: 124px;
    height: 124px;
    transform: rotate(45deg);
    background: var(--tile-white);
    border: 2px solid var(--tile-border);
    border-radius: 6px;
    box-shadow: 0 0 10px rgba(0,0,0,0.18);
    padding: 6px;
  }
  .tile-photo {
    width: 100%;
    height: 100%;
    border-radius: 3px;
    background: radial-gradient(circle, var(--gold-light) 0%, var(--gold-dark) 55%, var(--tile-white) 90%);
  }
  .tile-top { left: 841px; top: 44px; }
  .tile-left { left: 735px; top: 145px; }
  .tile-right { left: 937px; top: 145px; }
  .tile-bottom { left: 841px; top: 240px; }
  .tile-right .tile-photo { background: radial-gradient(circle, #e88f78 0%, var(--gold-dark) 55%, var(--tile-white) 90%); }
  .tile-bottom .tile-photo { background: radial-gradient(circle, #c9416a 0%, var(--gold-dark) 55%, var(--tile-white) 90%); }
</style>
</head>
<body>
  <main class="banner">
    <div class="sale-label">MOTHER'S DAY SALE</div>
    <div class="save-line">Save <span class="discount">15%</span></div>
    <div class="promo-line">with Promo Code:</div>
    <div class="promo-code">LOVEMOM</div>

    <div class="tile tile-top"><div class="tile-photo" role="img" aria-label="Gold and diamond openwork band ring"></div></div>
    <div class="tile tile-left"><div class="tile-photo" role="img" aria-label="Pair of gold rope rings with diamond X motif"></div></div>
    <div class="tile tile-right"><div class="tile-photo" role="img" aria-label="Gold ring set with carved coral"></div></div>
    <div class="tile tile-bottom"><div class="tile-photo" role="img" aria-label="Gold crab brooch set with rubies"></div></div>
  </main>
</body>
</html>
```